Small Business Broker Business Card Design

A business card design for a small business brokerage, which is a financial service, not unlike real estate brokerage, but for small businesses such as laundromats, pizza shops, restaurants, cleaners etc. The designs should all be simple, more conservative in nature, using the colors and font of the logo. Again, think real estate Brokerage as a business context
Contact Information for Business Card
Name: Glen R. Harlow. Title: Small Business Advisor. Email: g.harlow@bayfieldcapitalworks.example. Mobile: (555) 274-3918. Office: (555) 806-2147. www.bayfieldcapitalworks.example

```html
<!DOCTYPE html>
<html lang="en">
<head>
<meta charset="utf-8">
<title>Bayfield Capital Works – Business Card</title>
<link rel="stylesheet" href="https://fonts.googleapis.com/css2?family=Montserrat:wght@400;500;700&display=swap">
<style>
  :root {
    --navy: #1b3a6b;
    --green: #8cc63f;
    --white: #ffffff;
    --ink: #1d1d1f;
    --backdrop: #ebebeb;
  }
  * { margin: 0; padding: 0; box-sizing: border-box; }
  html, body { width: 1093px; height: 1200px; overflow: hidden; }
  body {
    background: var(--backdrop);
    font-family: "Montserrat", Arial, sans-serif;
    position: relative;
  }
  .card {
    position: absolute;
    left: 265px;
    width: 582px;
    height: 364px;
    border-radius: 24px;
  }
  .card--front { top: 225px; background: var(--white); }
  .card--back { top: 616px; background: var(--navy); }

  .brand {
    position: absolute;
    display: flex;
    flex-direction: column;
    align-items: center;
    text-align: center;
  }
  .brand__mark { display: block; }
  .brand__name { font-weight: 700; white-space: nowrap; }
  .brand__tagline { font-weight: 500; color: var(--green); white-space: nowrap; text-transform: uppercase; }

  .card--front .brand { left: 22px; width: 238px; top: 150px; }
  .card--front .brand__mark { width: 22px; height: 22px; background: var(--navy); margin-bottom: 10px; }
  .card--front .brand__name { color: var(--navy); font-size: 13px; letter-spacing: 0.1px; }
  .card--front .brand__tagline { font-size: 6.5px; letter-spacing: 1px; margin-top: 2px; }

  .divider {
    position: absolute;
    left: 271px; top: 117px;
    width: 1.5px; height: 148px;
    background: var(--navy);
  }
  .person { position: absolute; left: 282px; top: 114px; }
  .person__name { color: var(--navy); font-size: 20px; font-weight: 700; line-height: 1.1; }
  .person__title { color: var(--ink); font-size: 13px; font-weight: 400; margin-top: 2px; }

  .contacts { position: absolute; left: 284px; top: 185px; list-style: none; }
  .contacts li {
    display: flex; align-items: center;
    font-size: 13px; color: var(--ink);
    height: 20px;
  }
  .contacts li + li { margin-top: 1px; }
  .contacts li:nth-child(2) { margin-top: 4px; }
  .contacts svg { width: 12px; height: 12px; margin-right: 9px; fill: var(--navy); flex: none; }

  .card--back .brand { left: 0; right: 0; top: 140px; }
  .card--back .brand__mark { width: 56px; height: 56px; background: var(--green); margin-bottom: 26px; }
  .card--back .brand__name { color: var(--white); font-size: 22px; letter-spacing: 0.3px; }
  .card--back .brand__tagline { font-size: 11.5px; letter-spacing: 1.9px; margin-top: 3px; }
</style>
</head>
<body>
  <section class="card card--front">
    <div class="brand">
      <span class="brand__mark"></span>
      <span class="brand__name">BAYFIELD CAPITAL WORKS, INC</span>
      <span class="brand__tagline">Trusted guidance to buy or sell your business</span>
    </div>
    <span class="divider"></span>
    <div class="person">
      <h1 class="person__name">Glen R. Harlow</h1>
      <p class="person__title">Small Business Advisor</p>
    </div>
    <ul class="contacts">
      <li>
        <svg viewBox="0 0 24 24" aria-hidden="true"><path d="M2 9c0-3 5-5 10-5s10 2 10 5v2h-5V9.5c-1.5-.6-3.2-.9-5-.9s-3.5.3-5 .9V11H2zM6 12l3-3h6l3 3 2 8H4zm6 1.5a2.5 2.5 0 1 0 0 5 2.5 2.5 0 0 0 0-5z"/></svg>
        (555) 806-2147
      </li>
      <li>
        <svg viewBox="0 0 24 24" aria-hidden="true"><path d="M6.6 10.8a15 15 0 0 0 6.6 6.6l2.2-2.2c.3-.3.7-.4 1-.2 1.1.4 2.3.6 3.6.6.6 0 1 .4 1 1V20c0 .6-.4 1-1 1A17 17 0 0 1 3 4c0-.6.4-1 1-1h3.5c.6 0 1 .4 1 1 0 1.3.2 2.5.6 3.6.1.3 0 .7-.2 1zM14 2a8 8 0 0 1 8 8h-2a6 6 0 0 0-6-6zm0 4a4 4 0 0 1 4 4h-2a2 2 0 0 0-2-2z"/></svg>
        (555) 274-3918
      </li>
      <li>
        <svg viewBox="0 0 24 24" aria-hidden="true"><path d="M2 5h20v2l-10 6L2 7zm0 4.3l10 6 10-6V19H2z"/></svg>
        g.harlow@bayfieldcapitalworks.example
      </li>
      <li>
        <svg viewBox="0 0 24 24" aria-hidden="true"><path d="M12 2a10 10 0 1 0 0 20 10 10 0 0 0 0-20zm-1 17.9A8 8 0 0 1 4.2 10.2L9 15v1a2 2 0 0 0 2 2zm6.9-2.5A2 2 0 0 0 16 16h-1v-3a1 1 0 0 0-1-1H8v-2h2a1 1 0 0 0 1-1V7h2a2 2 0 0 0 2-2v-.4a8 8 0 0 1 2.9 12.8z"/></svg>
        www.bayfieldcapitalworks.example
      </li>
    </ul>
  </section>

  <section class="card card--back">
    <div class="brand">
      <span class="brand__mark"></span>
      <span class="brand__name">BAYFIELD CAPITAL WORKS, INC</span>
      <span class="brand__tagline">Trusted guidance to buy or sell your business</span>
    </div>
  </section>
</body>
</html>
```